Sports League Registration Banner for facebook

I have a graphic with a basic idea for an ad that I would like to post on facebook but I need it to be reconfigured to fit their dimensions (1194 by 624, or in that ratio) and to have the text moved and placed in another spot on the ad. I also want the colors to be changed to look like my website (www.brq-leagues.net) but no logo on the ad. This is to promote registration for a sports league.

The idea is basically to get up off the couch and play some sports. The text on the bottom should be moved off to the side and replaced with:

GET FIT HAVE FUN
10 Game Season + Playoffs
1 Game per week
Team Fee $1525
Player Fee $125

Men's Ball Hockey

Industry/Entity Type

Graphic Design

```html
<!DOCTYPE html>
<html lang="en">
<head>
<meta charset="utf-8">
<title>Men's Ball Hockey – Get Fit Have Fun</title>
<link rel="stylesheet" href="https://fonts.googleapis.com/css2?family=Oswald:wght@500;700&family=Tinos:wght@700&display=swap">
<style>
  :root {
    --lime: #86e234;
    --lime-light: #a4ef5c;
    --lime-pale: #dcf6c2;
    --badge-green: #7fd43a;
    --ink: #0d0d0d;
    --white: #ffffff;
    --photo-dark: #2e2118;
    --photo-mid: #6b4a30;
    --photo-warm: #a8795a;
  }
  * { margin: 0; padding: 0; box-sizing: border-box; }
  html, body { width: 1200px; height: 627px; overflow: hidden; }
  body { background: var(--lime); }

  .banner {
    position: relative;
    width: 1200px;
    height: 627px;
    overflow: hidden;
    background: radial-gradient(ellipse at 58% 70%, var(--lime-light) 0%, var(--lime) 65%);
  }

  .photo-card {
    position: absolute;
    left: 30px;
    top: 62px;
    width: 582px;
    height: 432px;
    background: var(--lime-pale);
    border-radius: 18px;
    padding: 22px;
    transform: rotate(-4deg);
    box-shadow: 4px 8px 18px rgba(0,0,0,0.35);
  }
  .photo-card__image {
    width: 100%;
    height: 100%;
    background: linear-gradient(135deg, var(--photo-mid) 0%, var(--photo-dark) 45%, var(--photo-warm) 70%, var(--photo-dark) 100%);
  }

  .never-late-badge {
    position: absolute;
    left: 45px;
    top: 380px;
    width: 196px;
    height: 196px;
    transform: rotate(-8deg);
    filter: drop-shadow(2px 4px 5px rgba(0,0,0,0.3));
  }
  .never-late-badge__text {
    font-family: 'Oswald', sans-serif;
    font-weight: 700;
    fill: var(--badge-green);
    text-anchor: middle;
  }

  .league-info {
    position: absolute;
    left: 688px;
    top: 75px;
    color: var(--ink);
  }
  .league-info__headline {
    font-family: 'Tinos', serif;
    font-weight: 700;
    font-size: 41px;
    color: var(--white);
    letter-spacing: 4.5px;
    white-space: nowrap;
    text-shadow: 2px 2px 3px rgba(0,0,0,0.45);
    margin-bottom: 50px;
    margin-left: -2px;
  }
  .league-info__list { list-style: none; }
  .league-info__item {
    font-family: 'Oswald', sans-serif;
    font-weight: 500;
    font-size: 37px;
    letter-spacing: 2.5px;
    white-space: nowrap;
    line-height: 1;
    margin-bottom: 46px;
  }
</style>
</head>
<body>
  <main class="banner">
    <figure class="photo-card">
      <div class="photo-card__image" role="img" aria-label="Photo of a man lounging on a couch with a beer and a burger beside an old television"></div>
    </figure>

    <svg class="never-late-badge" viewBox="0 0 200 200" aria-label="It's never too late">
      <polygon fill="#ffffff" points="198,100 183,113.1 193.2,130.3 174.8,138.1 179.3,157.6 159.4,159.4 157.6,179.3 138.1,174.8 130.3,193.2 113.1,183 100,198 86.9,183 69.7,193.2 61.9,174.8 42.4,179.3 40.6,159.4 20.7,157.6 25.2,138.1 6.8,130.3 17,113.1 2,100 17,86.9 6.8,69.7 25.2,61.9 20.7,42.4 40.6,40.6 42.4,20.7 61.9,25.2 69.7,6.8 86.9,17 100,2 113.1,17 130.3,6.8 138.1,25.2 157.6,20.7 159.4,40.6 179.3,42.4 174.8,61.9 193.2,69.7 183,86.9"/>
      <g transform="rotate(-10 100 100)">
        <text class="never-late-badge__text" x="96" y="66" font-size="30">IT'S</text>
        <text class="never-late-badge__text" x="100" y="102" font-size="34">NEVER</text>
        <text class="never-late-badge__text" x="104" y="132" font-size="28">TOO</text>
        <text class="never-late-badge__text" x="106" y="166" font-size="34">LATE</text>
      </g>
    </svg>

    <section class="league-info">
      <h1 class="league-info__headline">GET FIT HAVE FUN!</h1>
      <ul class="league-info__list">
        <li class="league-info__item">10 Game Season + Playoffs</li>
        <li class="league-info__item">1 Game per week</li>
        <li class="league-info__item">Team Fee $1525</li>
        <li class="league-info__item">Player Fee $125</li>
      </ul>
    </section>
  </main>
</body>
</html>
```